Bright Wave Labs

We need a professional letter head format for our company. Now we have a logo but need to desing a new logo also. I have uploaded our old logo. Use the color in the logo and design a new one.

Dear Designers , Need to mention "BWL" and please dont use our old LOGO. we need a new catchy one.

```html
<!DOCTYPE html>
<html lang="en">
<head>
<meta charset="utf-8">
<title>Bright Wave Labs – Letterhead</title>
<link rel="stylesheet" href="https://fonts.googleapis.com/css2?family=Open+Sans:wght@400;600&family=Lato:wght@400;700&display=swap">
<style>
  :root {
    --navy: #172c45;
    --lime: #8dc02c;
    --ink: #3d3d3d;
    --ink-dark: #1e1e1e;
    --rule: #8a9099;
    --paper: #ffffff;
    --backdrop: #e4e4e4;
  }
  * { margin: 0; padding: 0; box-sizing: border-box; }
  html, body { width: 1040px; height: 1200px; overflow: hidden; background: var(--backdrop); }
  .letterhead {
    position: absolute; left: 70px; top: 20px;
    width: 900px; height: 1160px;
    background: var(--paper);
    box-shadow: 0 2px 10px rgba(0,0,0,0.12);
    font-family: "Open Sans", Arial, sans-serif;
    color: var(--ink);
  }
  .brand {
    position: absolute; top: 110px; left: 0; width: 100%;
    font-family: "Open Sans", Arial, sans-serif;
    font-weight: 600; font-size: 27px; line-height: 40px; color: var(--navy);
    display: flex; justify-content: center; align-items: center; gap: 12px;
  }
  .brand-square { width: 18px; height: 18px; background: var(--lime); }
  .letter { position: absolute; left: 85px; width: 727px; font-size: 14px; }
  .issue-date { top: 240px; }
  .recipient { top: 284px; line-height: 17px; }
  .greeting { top: 372px; }
  .body-copy { top: 421px; line-height: 26.2px; text-align: justify; hyphens: manual; }
  .body-copy p + p { margin-top: 26.2px; }
  .closing { top: 814px; }
  .signatory { top: 886px; }
  .signatory-name { font-size: 17px; font-weight: 600; color: var(--ink-dark); }
  .signatory-role { font-size: 14px; margin-top: 4px; }
  .footer-address {
    position: absolute; top: 1072px; left: 0; width: 100%;
    text-align: center; font-family: "Lato", Arial, sans-serif;
    font-size: 16px; color: var(--ink-dark);
  }
  .footer-rule { position: absolute; top: 1101px; left: 156px; width: 586px; height: 1px; background: var(--rule); }
  .footer-contact {
    position: absolute; top: 1110px; left: 0; width: 100%;
    text-align: center; font-family: "Lato", Arial, sans-serif;
    font-size: 16px; color: var(--ink-dark); word-spacing: 1px;
  }
  .footer-contact .sep { margin: 0 22px; color: var(--ink-dark); }
  .footer-band { position: absolute; left: 0; bottom: 3px; width: 900px; height: 14px; }
</style>
</head>
<body>
<main class="letterhead">
  <div class="brand"><span class="brand-square"></span>Bright Wave Labs</div>

  <p class="letter issue-date">Issuing Date: May 5, 2018</p>
  <p class="letter recipient">Name Of Employee Mr. XYZABC<br>Address of Employee<br>Address Line 2 etc..</p>
  <p class="letter greeting">Dear Mr.XYZABC</p>

  <div class="letter body-copy">
    <p>Lorem Ipsum has been the industry's standard dummy text ever since the 1500s, when an unknown printer took a galley of type and scrambled it to make a type specimen book. It has survived not only five centuries, but also the leap into electronic typesetting, remaining essentially unchanged. It was popularised in the 1960s with the release of Typeline sheets containing Lorem Ipsum passages, and more recently with desktop pub&shy;lishing software like PageForge Studio including versions of Lorem Ipsum.</p>
    <p>Lorem Ipsum is simply dummy text of the printing and typesetting industry. Lorem Ipsum has been the indus&shy;try's standard dummy text ever since the 1500s, when an unknown printer took a galley of type and scram&shy;bled it to make a type specimen book.</p>
    <p>It has survived not only five centuries, but also the leap into electronic typesetting, remaining essentially un&shy;changed. It was popularised in the 1960s with the release of Typeline sheets containing Lorem IpsumIpsum passages.</p>
  </div>

  <p class="letter closing">Yours Sincerely</p>
  <div class="letter signatory">
    <p class="signatory-name">Daniel Hart</p>
    <p class="signatory-role">Managing Director</p>
  </div>

  <p class="footer-address">421, Address line here, 45452,Country Name</p>
  <div class="footer-rule"></div>
  <p class="footer-contact">P: 044-555 210 347<span class="sep">|</span>E: hello@brightwavelabs.com<span class="sep">|</span>www.brightwavelabs.com</p>

  <svg class="footer-band" viewBox="0 0 900 14" preserveAspectRatio="none" aria-hidden="true">
    <polygon points="0,0 449,0 458,14 0,14" fill="var(--navy)"/>
    <polygon points="452,0 900,0 900,14 461,14" fill="var(--lime)"/>
  </svg>
</main>
</body>
</html>
```